New Business Card Design Project

Use the flyer uploaded and website www.brightoakbuilders.com for inspiration.
List Our Services on Backside of business cards
Marcus Delling
Harborline Builders Inc.
Licensed General Contractors
858-471-6093

Contact Information for Business Card

Use the flyer uploaded and website www.brightoakbuilders.com for inspiration. List Our Services on Backside of business cards Marcus Delling Harborline Builders Inc. Licensed General Contractors 858-471-6093

```html
<!DOCTYPE html>
<html lang="en">
<head>
<meta charset="UTF-8">
<title>Harborline Builders – Business Card</title>
<link rel="stylesheet" href="https://fonts.googleapis.com/css2?family=Cormorant+Garamond:wght@500&family=Arimo:wght@400&display=swap">
<style>
  :root {
    --page: #dcdcdc;
    --card: #323232;
    --ink: #ffffff;
    --band: #e4e4e8;
    --font-serif: "Cormorant Garamond", serif;
    --font-sans: "Arimo", sans-serif;
  }
  * { box-sizing: border-box; margin: 0; padding: 0; }
  html, body { width: 1200px; height: 1040px; overflow: hidden; }
  body { background: var(--page); position: relative; font-family: var(--font-sans); color: var(--ink); }

  .card {
    position: absolute;
    background: var(--card);
    border-radius: 16px;
    overflow: hidden;
    box-shadow: 0 2px 6px rgba(0,0,0,0.25);
  }
  .card-front { left: 285px; top: 130px; width: 641px; height: 366px; }
  .card-back  { left: 285px; top: 568px; width: 645px; height: 368px; }

  /* Front */
  .brand-name {
    position: absolute;
    font-family: var(--font-serif);
    font-weight: 500;
    color: var(--ink);
    text-transform: uppercase;
    white-space: nowrap;
    transform: translateX(-50%);
  }
  .card-front .brand-name { left: 479px; top: 134px; font-size: 22px; letter-spacing: 1px; }

  .person-name {
    position: absolute; left: 42px; top: 220px;
    font-family: var(--font-serif); font-weight: 500;
    font-size: 27px; letter-spacing: 0.5px; text-transform: uppercase;
  }
  .name-rule { position: absolute; left: 42px; top: 259px; width: 554px; height: 1px; background: #bdbdbd; }

  .contact-list { position: absolute; left: 42px; top: 268px; list-style: none; }
  .contact-list li { display: flex; align-items: center; height: 20px; font-size: 16px; }
  .contact-list svg { width: 13px; height: 13px; margin-right: 8px; fill: var(--ink); }

  .company-info { position: absolute; right: 45px; top: 268px; text-align: right; font-size: 16px; line-height: 20px; }

  .bottom-band { position: absolute; left: 0; right: 0; bottom: 0; height: 21px; background: var(--band); border-top: 3px solid #ffffff; }
  .bottom-band::before { content: ""; position: absolute; left: 0; right: 0; top: 0; height: 3px; background: #9a9a9e; }

  /* Back */
  .card-back .brand-name { left: 50%; top: 92px; font-size: 30px; letter-spacing: 1.5px; }
  .services-title {
    position: absolute; left: 0; right: 0; top: 217px; text-align: center;
    font-family: var(--font-serif); font-weight: 500; font-size: 21px; letter-spacing: 3px;
  }
  .services-list { position: absolute; left: 0; right: 0; top: 253px; list-style: none; text-align: center; }
  .services-list li { font-size: 16px; line-height: 23.5px; white-space: nowrap; }
  .sep { display: inline-block; width: 7px; height: 7px; background: var(--ink); margin: 0 9px; vertical-align: 2px; }
</style>
</head>
<body>

<section class="card card-front" aria-label="Business card front">
  <div class="brand-name">Harborline Builders</div>

  <h1 class="person-name">Marcus Delling</h1>
  <div class="name-rule"></div>

  <ul class="contact-list">
    <li>
      <svg viewBox="0 0 24 24" aria-hidden="true"><path d="M6.6 10.8a15.1 15.1 0 0 0 6.6 6.6l2.2-2.2c.3-.3.7-.4 1-.2 1.1.4 2.3.6 3.6.6.6 0 1 .4 1 1V20c0 .6-.4 1-1 1C10.6 21 3 13.4 3 4c0-.6.4-1 1-1h3.5c.6 0 1 .4 1 1 0 1.3.2 2.5.6 3.6.1.3 0 .7-.2 1z"/></svg>
      858-471-6093
    </li>
    <li>
      <svg viewBox="0 0 24 24" aria-hidden="true"><path d="M2 5h20v14H2z M4 7v.3l8 5.2 8-5.2V7z" fill-rule="evenodd"/></svg>
      info@brightoakbuilders.com
    </li>
    <li>
      <svg viewBox="0 0 24 24" aria-hidden="true"><circle cx="12" cy="12" r="10"/><path d="M7 8c2 0 3 1 3 3s2 2 2 4-1 3-1 4M14 4c0 2 2 2 3 3s3 1 3 3" stroke="#323232" stroke-width="1.6" fill="none"/></svg>
      www.brightoakbuilders.com
    </li>
  </ul>

  <div class="company-info">
    <div>Harborline Builders Inc.</div>
    <div>Licensed General Contractors</div>
  </div>

  <div class="bottom-band"></div>
</section>

<section class="card card-back" aria-label="Business card back">
  <div class="brand-name">Harborline Builders</div>
  <h2 class="services-title">SERVICES</h2>
  <ul class="services-list">
    <li>Remodel : Kitchen &amp; Bath<span class="sep"></span>Painting : Interior &amp; Exterior</li>
    <li>Flooring : Carpet, Vinyl, Wood<span class="sep"></span>Window &amp; Door Replacement</li>
    <li>Plumbing : Repairs &amp; Upgrades<span class="sep"></span>Energy- Efficient Upgrades</li>
    <li>Deck &amp; Pation Construction<span class="sep"></span>Water &amp; Mold Damage<span class="sep"></span>Garage Renovation</li>
  </ul>
</section>

</body>
</html>
```